Business cards to launch an education platform

Hi,
I am looking at having new business cards designed.
I am a startup, developing a web platform for schools and university, the education world. It's an online assessment system.
I would like a card that looks classy, and that is using the colors and the font of my logo.

I have attached:
1) my logo
2) A business card that I have designed quickly so you can have all the information required in the card, but I really don't like it.
3) The font that I am using (Lato Regular) to design my web platform
4) Some screenshots of my web platform so you can have a look at the style that I have.

Target Market(s)

Major market: Education system: Schools and university
Minor markets: Business in general

Industry/Entity Type

Business

Contact Information for Business Card

Clara Fenwick
Director

M: 0437 518 902
E: clara.fenwick@amberLoomSystems.com.au

Requirements
Must have
• The colors of my logo

```html
<!DOCTYPE html>
<html lang="en">
<head>
<meta charset="utf-8">
<title>Amber Loom Systems – Business Cards</title>
<link href="https://fonts.googleapis.com/css2?family=Lato:wght@400;700&display=swap" rel="stylesheet">
<style>
  :root {
    --navy: #1c4178;
    --mid-blue: #1b75bb;
    --sky-blue: #27a6df;
    --card-black: #111113;
    --paper: #ffffff;
    --backdrop: #e9e7e3;
    --ink-white: #f4f4f4;
  }
  * { margin: 0; padding: 0; box-sizing: border-box; }
  html, body {
    width: 1200px;
    height: 900px;
    overflow: hidden;
    background: var(--backdrop);
    font-family: "Lato", sans-serif;
  }
  .canvas {
    position: relative;
    width: 1200px;
    height: 900px;
  }
  .card {
    position: absolute;
    left: 280px;
    width: 640px;
    height: 366px;
    overflow: hidden;
    box-shadow: 0 6px 18px rgba(0,0,0,0.18);
  }

  /* Back of card */
  .card-back {
    top: 46px;
    background: var(--card-black);
    display: flex;
    flex-direction: column;
    align-items: center;
    justify-content: center;
    color: var(--ink-white);
    font-weight: 400;
  }
  .card-back .brand-line-1 {
    font-size: 58px;
    letter-spacing: 10px;
    line-height: 1;
  }
  .card-back .brand-line-2 {
    font-size: 40px;
    letter-spacing: 8px;
    line-height: 1.15;
    margin-top: 4px;
  }

  /* Front of card */
  .card-front {
    top: 488px;
    background: var(--paper);
  }
  .card-front .decor {
    position: absolute;
    inset: 0;
    width: 640px;
    height: 366px;
  }
  .holder {
    position: absolute;
    left: 60px;
    top: 24px;
  }
  .holder-name {
    color: var(--sky-blue);
    font-size: 19px;
    font-weight: 400;
    letter-spacing: 0.3px;
    line-height: 1.1;
  }
  .holder-title {
    color: var(--navy);
    font-size: 11px;
    font-weight: 700;
    margin-top: 1px;
  }
  .brand-block {
    position: absolute;
    right: 192px;
    top: 142px;
    text-align: center;
    color: var(--navy);
    font-weight: 400;
  }
  .brand-block .brand-line-1 {
    font-size: 34px;
    letter-spacing: 5px;
    line-height: 1;
  }
  .brand-block .brand-line-2 {
    font-size: 20px;
    letter-spacing: 4px;
    line-height: 1.2;
    margin-top: 2px;
  }
  .brand-divider {
    position: absolute;
    left: 462px;
    top: 128px;
    width: 2px;
    height: 104px;
    background: var(--sky-blue);
  }
  .brand-square {
    position: absolute;
    left: 484px;
    top: 146px;
    width: 66px;
    height: 66px;
    background: var(--mid-blue);
  }
  .contacts {
    position: absolute;
    left: 30px;
    top: 214px;
    list-style: none;
    color: var(--navy);
    font-size: 14px;
    line-height: 20px;
  }
  .contacts li {
    display: flex;
    align-items: center;
    gap: 8px;
  }
  .contacts svg { flex: none; }
</style>
</head>
<body>
<main class="canvas">

  <section class="card card-back" aria-label="Business card back">
    <div class="brand-line-1">AMBER</div>
    <div class="brand-line-2">Loom Systems</div>
  </section>

  <section class="card card-front" aria-label="Business card front">
    <svg class="decor" viewBox="0 0 640 366" aria-hidden="true">
      <polygon points="0,0 44,0 30,26 0,26" fill="var(--mid-blue)"/>
      <polygon points="18,26 44,0 44,26" fill="var(--navy)"/>
      <polygon points="0,262 236,300 214,320 0,288" fill="var(--mid-blue)"/>
      <polygon points="226,302 640,326 640,366 198,366" fill="var(--navy)"/>
    </svg>

    <div class="holder">
      <div class="holder-name">Clara Fenwick</div>
      <div class="holder-title">Director</div>
    </div>

    <div class="brand-block">
      <div class="brand-line-1">AMBER</div>
      <div class="brand-line-2">Loom Systems</div>
    </div>
    <div class="brand-divider"></div>
    <div class="brand-square"></div>

    <ul class="contacts">
      <li>
        <svg width="12" height="12" viewBox="0 0 24 24" aria-hidden="true">
          <path fill="var(--mid-blue)" d="M6.6 10.8a15.2 15.2 0 0 0 6.6 6.6l2.2-2.2a1 1 0 0 1 1-.25 11.4 11.4 0 0 0 3.6.57 1 1 0 0 1 1 1V20a1 1 0 0 1-1 1A17 17 0 0 1 3 4a1 1 0 0 1 1-1h3.5a1 1 0 0 1 1 1c0 1.25.2 2.45.57 3.57a1 1 0 0 1-.25 1z"/>
        </svg>
        <span>0437 518 902</span>
      </li>
      <li>
        <svg width="12" height="10" viewBox="0 0 24 18" aria-hidden="true">
          <rect x="1" y="1" width="22" height="16" rx="1.5" fill="none" stroke="var(--mid-blue)" stroke-width="2"/>
          <path d="M2 2l10 8 10-8" fill="none" stroke="var(--mid-blue)" stroke-width="2"/>
        </svg>
        <span>clara.fenwick@amberLoomSystems.com.au</span>
      </li>
    </ul>
  </section>

</main>
</body>
</html>
```